High-end construction company needs a business card design

We need a modern looking business card that draws people in, is memorable and looks so good people will want to sick it on their fridges.
On the first side what is needed are:
Logo
My name - Tomasz Brelwik
Title - Managing Director
Website - www.varkelt.co.uk
Email - tomasz@varkelt.co.uk
Telephone - 020 5194 6281
Mobile - 07845139072
On the back side was is needed is a list of all the services we provide:
-Kitchen Renovations
-Bathroom Renovations
-House Renovations
-Garage Conversions
-Extensions
-Loft Conversions
-Conservatories
-Carpentry
-Tiling
-Electrical
-Plumbing & Heating
-Bricklaying
-Landscaping
-Decorating
-Plastering
We would like the colours to be the same shades as on the logo with grey or black for the words.
Target Market(s)
Anyone who needs building work done
Contact Information for Business Card
This business card is for a construction company which strives to deliver excellent service and quality.
The look and feel of the card should represent this.
Requirements
Must have
- On the first side what is needed are:
Logo
My name - Tomasz Brelwik
Title - Managing Director
Website - www.varkelt.co.uk
Email - tomasz@varkelt.co.uk
Telephone - 020 5194 6281
Mobile - 07845139072
Nice to have
- Cool looking features

```html
<!DOCTYPE html>
<html lang="en">
<head>
<meta charset="utf-8">
<title>Varkelt Construction Ltd — Business Card</title>
<link rel="stylesheet" href="https://fonts.googleapis.com/css2?family=Exo+2:wght@400;500;800&display=swap">
<style>
  :root {
    --page-bg: #d9d3cb;
    --card-top: #f4f6f7;
    --card-bottom: #e6e9ea;
    --green-deep: #1f5a22;
    --green-mid: #2f7a2f;
    --green-bright: #4f9f36;
    --text-grey: #4a4d50;
    --text-dark: #2b2d2f;
  }
  * { box-sizing: border-box; margin: 0; padding: 0; }
  html, body {
    width: 1200px; height: 970px; overflow: hidden;
    background: var(--page-bg);
    font-family: "Exo 2", sans-serif;
  }
  .canvas { position: relative; width: 1200px; height: 970px; }
  .business-card {
    position: absolute; left: 80px; top: 190px;
    width: 1040px; height: 590px;
    border-radius: 24px; overflow: hidden;
    background: linear-gradient(180deg, var(--card-top), var(--card-bottom));
    box-shadow: 0 10px 30px rgba(0,0,0,0.18);
  }
  .card-swooshes { position: absolute; inset: 0; }
  .wordmark {
    position: absolute; left: 590px; top: 150px; width: 400px;
    text-align: right; color: var(--green-mid); font-weight: 800;
  }
  .wordmark-name { font-size: 92px; line-height: 1; letter-spacing: 2px; }
  .wordmark-sub { font-size: 26px; letter-spacing: 4px; margin-top: 8px; }
  .person-name {
    position: absolute; left: 48px; top: 326px;
    font-size: 34px; font-weight: 800; color: var(--green-bright);
    letter-spacing: 1px; text-transform: uppercase;
  }
  .person-title {
    position: absolute; left: 49px; top: 372px;
    font-size: 24px; font-weight: 500; color: var(--text-grey);
  }
  .contact-list {
    position: absolute; top: 436px; list-style: none;
  }
  .contact-list li {
    display: flex; align-items: center; height: 33px;
    font-size: 25px; color: var(--text-grey); letter-spacing: 0.5px;
  }
  .contact-icon { width: 24px; height: 24px; margin-right: 14px; flex: none; }
  .contact-phones { left: 50px; }
  .contact-web { left: 378px; }
  .contact-divider {
    position: absolute; left: 332px; top: 440px;
    width: 2px; height: 60px; background: var(--text-grey);
  }
</style>
</head>
<body>
<main class="canvas">
  <section class="business-card">
    <svg class="card-swooshes" viewBox="0 0 1040 590" width="1040" height="590" aria-hidden="true">
      <path d="M0 0 H470 C300 20 120 70 0 130 Z" fill="var(--green-mid)"/>
      <path d="M0 142 C150 70 330 22 480 0 H505 C340 28 150 84 0 156 Z" fill="var(--green-bright)"/>
      <path d="M0 196 C160 100 350 36 540 0 H600 C400 46 180 128 0 228 Z" fill="var(--green-mid)"/>
      <path d="M0 505 C320 548 700 520 1040 500 V590 H0 Z" fill="var(--green-bright)"/>
      <path d="M0 530 C360 566 720 540 1040 515 V590 H0 Z" fill="var(--green-mid)"/>
      <path d="M0 560 C380 584 740 566 1040 540 V590 H0 Z" fill="var(--green-deep)"/>
    </svg>

    <div class="wordmark">
      <div class="wordmark-name">VARKELT</div>
      <div class="wordmark-sub">CONSTRUCTION LTD</div>
    </div>

    <h1 class="person-name">Tomasz Brelwik</h1>
    <p class="person-title">Managing Director</p>

    <ul class="contact-list contact-phones">
      <li>
        <svg class="contact-icon" viewBox="0 0 24 24"><circle cx="12" cy="12" r="12" fill="var(--green-bright)"/><path d="M8 6 L10 6 L11 9 L9.5 10.5 C10.3 12.2 11.8 13.7 13.5 14.5 L15 13 L18 14 L18 16 C18 17 17 18 16 18 C10.5 17.6 6.4 13.5 6 8 C6 7 7 6 8 6 Z" fill="#fff"/></svg>
        020 5194 6281
      </li>
      <li>
        <svg class="contact-icon" viewBox="0 0 24 24"><circle cx="12" cy="12" r="12" fill="var(--green-bright)"/><rect x="8" y="5" width="8" height="14" rx="1.5" fill="#fff"/><rect x="9.3" y="7" width="5.4" height="8.5" fill="var(--green-bright)"/></svg>
        07845139072
      </li>
    </ul>
    <span class="contact-divider"></span>
    <ul class="contact-list contact-web">
      <li>
        <svg class="contact-icon" viewBox="0 0 24 24"><circle cx="12" cy="12" r="12" fill="var(--green-bright)"/><rect x="6" y="8" width="12" height="8.5" fill="#fff"/><path d="M6 8 L12 13 L18 8" fill="none" stroke="var(--green-bright)" stroke-width="1.3"/></svg>
        tomasz@varkelt.co.uk
      </li>
      <li>
        <svg class="contact-icon" viewBox="0 0 24 24"><circle cx="12" cy="12" r="12" fill="var(--green-bright)"/><g fill="none" stroke="#fff" stroke-width="1.3"><circle cx="12" cy="12" r="6"/><ellipse cx="12" cy="12" rx="2.6" ry="6"/><path d="M6 12 H18"/></g></svg>
        www.varkelt.co.uk
      </li>
    </ul>
  </section>
</main>
</body>
</html>
```